Create modern and sleek business card for luxury real estate company

We're a "boutique" real estate office looking for a design that gets across a highly modern luxury brand. Blacks and whites are probably the best colors unless we try a silver foil for the logo. I've attached a version of our current logo here. I'd like to swap out the current font on there with Gotham Light Regular.

I'm looking to have one side of the card have the logo with the space for our agents info on the other side.

Target Market(s)

Young professionals in a "luxury" headspace

Industry/Entity Type

Real estate

Contact Information for Business Card

A place for agent name, cell number, website. The slogan "Simply Rethinking Real Estate".

Font styles to use
Other font styles liked:
• Gotham Regular

Colors

Designer to choose only greyscale colors for use in the design.

Requirements
Must have
• Matte black as the background color. Clean lines and use of contrast. A specific design aspect that will use silver foil.
Nice to have
• Up in the air on integrating a QR code
Should not have
• Any houses or other real estate related design (ex: a clip art house)

```html
<!DOCTYPE html>
<html lang="en">
<head>
<meta charset="utf-8">
<title>Halden Estates — Business Card</title>
<link rel="stylesheet" href="https://fonts.googleapis.com/css2?family=Tinos:wght@400;700&family=Lato:wght@400&display=swap">
<style>
  :root {
    --backdrop: #2a2a2a;
    --card-black: #161616;
    --pattern-dark: #121212;
    --pattern-light: #1f1f1f;
    --ink-white: #f4f4f4;
    --ink-soft: #d9d9d9;
    --rule-grey: #6b6b6b;
  }
  html, body {
    margin: 0;
    padding: 0;
    width: 1200px;
    height: 1108px;
    overflow: hidden;
    background: var(--backdrop);
  }
  .canvas {
    position: relative;
    width: 1200px;
    height: 1108px;
  }
  .card {
    position: absolute;
    top: 194px;
    width: 480px;
    height: 720px;
    border-radius: 26px;
    background: var(--card-black);
    box-shadow: 0 18px 40px rgba(0,0,0,0.45);
    overflow: hidden;
  }
  .card--front { left: 90px; }
  .card--back { left: 630px; }

  /* Front */
  .brand {
    position: absolute;
    top: 96px;
    left: 0;
    right: 0;
    display: flex;
    align-items: center;
    justify-content: center;
    gap: 22px;
  }
  .brand__circle {
    width: 92px;
    height: 92px;
    border-radius: 50%;
    border: 3px solid var(--ink-white);
    box-sizing: border-box;
  }
  .brand__name {
    font-family: "Tinos", serif;
    font-weight: 400;
    font-size: 44px;
    line-height: 1.02;
    letter-spacing: 1px;
    color: var(--ink-white);
    text-transform: uppercase;
  }
  .agent {
    position: absolute;
    top: 388px;
    left: 0;
    right: 0;
    text-align: center;
  }
  .agent__name {
    font-family: "Tinos", serif;
    font-weight: 700;
    font-size: 32px;
    letter-spacing: 1px;
    color: var(--ink-white);
    margin: 0;
  }
  .agent__title {
    font-family: "Lato", sans-serif;
    font-size: 19px;
    color: var(--ink-soft);
    margin: 2px 0 0;
  }
  .contact-icons {
    margin: 18px auto 0;
    width: 300px;
    display: flex;
    align-items: center;
    justify-content: center;
    gap: 8px;
  }
  .contact-icons::before,
  .contact-icons::after {
    content: "";
    flex: 1;
    height: 1px;
    background: var(--rule-grey);
  }
  .contact-icons::before { margin-right: 6px; }
  .contact-icons::after { margin-left: 6px; }
  .icon-tile {
    width: 30px;
    height: 30px;
    border-radius: 5px;
    background: var(--ink-white);
    display: flex;
    align-items: center;
    justify-content: center;
  }
  .contact-lines {
    font-family: "Lato", sans-serif;
    font-size: 20px;
    line-height: 1.3;
    color: var(--ink-white);
    margin: 10px 0 0;
  }
  .rule {
    width: 300px;
    height: 1px;
    background: var(--rule-grey);
    margin: 12px auto;
  }

  /* Back */
  .emblem-field {
    position: absolute;
    inset: 0;
    background: radial-gradient(circle at 70% 20%, var(--pattern-light), var(--pattern-dark) 70%);
  }
  .back-mark {
    position: absolute;
    left: 0;
    right: 0;
    top: 560px;
    display: flex;
    align-items: center;
    justify-content: center;
    gap: 10px;
  }
  .back-mark__circle {
    width: 24px;
    height: 24px;
    border-radius: 50%;
    border: 2px solid var(--ink-white);
    box-sizing: border-box;
  }
  .back-mark__name {
    font-family: "Tinos", serif;
    font-weight: 400;
    font-size: 16px;
    letter-spacing: 2px;
    text-transform: uppercase;
    color: var(--ink-white);
  }
</style>
</head>
<body>
<main class="canvas">
  <section class="card card--front" aria-label="Card front with agent details">
    <div class="brand">
      <div class="brand__circle"></div>
      <div class="brand__name">Halden<br>Estates</div>
    </div>

    <div class="agent">
      <h1 class="agent__name">JULIAN MARSH</h1>
      <p class="agent__title">Managing Director</p>

      <div class="contact-icons">
        <span class="icon-tile" aria-label="Phone">
          <svg width="18" height="18" viewBox="0 0 24 24"><path d="M6.6 10.8a15 15 0 0 0 6.6 6.6l2.2-2.2a1 1 0 0 1 1-.25 11.4 11.4 0 0 0 3.6.57 1 1 0 0 1 1 1V20a1 1 0 0 1-1 1A17 17 0 0 1 3 4a1 1 0 0 1 1-1h3.5a1 1 0 0 1 1 1c0 1.25.2 2.45.57 3.6a1 1 0 0 1-.25 1z" fill="#161616"/></svg>
        </span>
        <span class="icon-tile" aria-label="Email">
          <svg width="18" height="18" viewBox="0 0 24 24"><rect x="3" y="6" width="18" height="12" fill="none" stroke="#161616" stroke-width="2"/><path d="M3 6l9 7 9-7" fill="none" stroke="#161616" stroke-width="2"/></svg>
        </span>
        <span class="icon-tile" aria-label="Website">
          <svg width="18" height="18" viewBox="0 0 24 24"><circle cx="12" cy="12" r="9" fill="none" stroke="#161616" stroke-width="2"/><path d="M3 12h18M12 3c3 3 3 15 0 18M12 3c-3 3-3 15 0 18" fill="none" stroke="#161616" stroke-width="1.5"/></svg>
        </span>
      </div>

      <p class="contact-lines">020-555 0148 37<br>hello@haldenhq.com<br>www.haldenestates.co</p>
      <div class="rule"></div>
      <p class="contact-lines">18 Carrow Lane, Suite 4<br>60210, Westmarch</p>
    </div>
  </section>

  <section class="card card--back" aria-label="Card back">
    <div class="emblem-field" role="img" aria-label="Tonal spot-gloss repeat pattern of the company emblem across the matte black card"></div>
    <div class="back-mark">
      <div class="back-mark__circle"></div>
      <span class="back-mark__name">Halden Estates</span>
    </div>
  </section>
</main>
</body>
</html>
```